High impact classy folder for an HVAC and Electrical contractor

We need a folder designed. It needs to be high impact and classy with a rich look to it. We want to cement our branding via the use of the folder so the look will need to have impact with use of our logo and colors.

We want to pull the entire brand look and feel together with this folder. We are going to be making other marketing materials and this is the start of a much larger project. In the ideal situation the winning desginer will continue on with the rest of the projects because they will know how to apply the brand look.

We want to give our local company the feel of a national franchise. Wherein the brand is very prominent and is repeated over and over again.

Use of logo and color scheme will be important.

We like dark backgrounds because they really make the logo pop.

Target Market(s)

homeowners

Font styles to use
Serif

Requirements
Must have
• Logo prominent on the front
• Our Tag Line:
• The Best Way To Live In New Jersey Is With Harbel"
• On the inside pockets:
• Our Phone number: 973-555-0148
• A message to our customers:
• We want to thank you for choosing Harbel Tradeworks today
• Our name says it all, because for over 30 years we have prided ourselves on delivering the best service and exceeding our customers' expectations everyday. Whether you need something fixed, replaced or upgraded, no matter how large or small, the dedicated and experts at Harbel Tradeworks are here to take care of you. Delivering the right solution for you the first time- everytime - and ensuring you are always 100% satisfied. If for any reason you want to speak with us, please do not hesitate to call or email. Thank you again for choosing Harbel Tradeworks.
• On the rear: a graphic that says 24-7 service
• A list of other services we provide:
• Solar
• Generators
• Home Security
• Home Automation
• Home Inspection
• Energy Audits
• 1 Day Bathroom remodles
• Basement Waterproofing
• Garage Doors
• Home Theaters
Nice to have
• I added photos of a flyer and of a mobile website to give an idea of the color scheme as well

```html
<!DOCTYPE html>
<html lang="en">
<head>
<meta charset="utf-8">
<title>Harbel Tradeworks — Presentation Folder</title>
<link href="https://fonts.googleapis.com/css2?family=Montserrat:ital,wght@0,400;0,500;0,600;0,700;1,700&display=swap" rel="stylesheet">
<style>
  :root {
    --crimson: #9a1b24;
    --crimson-deep: #7a121b;
    --crimson-light: #a8242e;
    --cream: #f8f0cf;
    --cream-deep: #efe3b6;
    --orange: #e8832e;
    --gold-text: #f3c98a;
    --ink-light: #fbeee0;
    --stage: #b9b9b9;
  }
  * { box-sizing: border-box; margin: 0; padding: 0; }
  html, body { width: 842px; height: 1200px; overflow: hidden; }
  body {
    background: var(--stage);
    font-family: "Montserrat", Arial, sans-serif;
    position: relative;
  }
  .spread {
    position: absolute;
    left: 41px;
    width: 760px;
    height: 507px;
    display: flex;
    box-shadow: 0 8px 22px rgba(0,0,0,.25);
  }
  .spread--outside { top: 40px; }
  .spread--inside { top: 630px; }
  .panel {
    position: relative;
    width: 380px;
    height: 507px;
    overflow: hidden;
  }

  /* Back cover */
  .panel--back {
    background: linear-gradient(160deg, var(--crimson-light) 0%, var(--crimson) 50%, var(--crimson-deep) 100%);
  }
  .brand-ghost {
    position: absolute;
    left: 0; right: 0;
    text-align: center;
    font-weight: 700;
    font-size: 44px;
    line-height: 1.05;
    letter-spacing: 1px;
  }
  .panel--back .brand-ghost { top: 120px; color: rgba(255,255,255,.06); }
  .services {
    position: absolute;
    left: 30px; right: 30px;
    bottom: 58px;
    text-align: center;
    color: var(--ink-light);
  }
  .services__title {
    display: flex; align-items: center; justify-content: center; gap: 8px;
    font-size: 9px; font-weight: 700; letter-spacing: .5px; margin-bottom: 6px;
  }
  .services__title::before, .services__title::after {
    content: ""; width: 26px; border-top: 1px solid var(--ink-light); border-bottom: 1px solid var(--ink-light); height: 3px;
  }
  .services__list { font-size: 9.5px; line-height: 1.45; font-weight: 500; }
  .services__badge {
    margin-top: 10px;
    font-size: 14px; font-weight: 700; font-style: italic;
  }

  /* Front cover */
  .panel--front {
    background: linear-gradient(150deg, var(--cream) 0%, var(--cream-deep) 100%);
  }
  .brand-mark {
    position: absolute;
    top: 130px; left: 0; right: 0;
    display: flex; flex-direction: column; align-items: center; gap: 12px;
  }
  .brand-mark__dot {
    width: 14px; height: 14px; border-radius: 50%; background: var(--crimson);
  }
  .brand-mark__name {
    color: var(--crimson);
    font-weight: 700;
    font-size: 34px;
    line-height: 1.1;
    text-align: center;
    letter-spacing: .5px;
  }
  .wave-band {
    position: absolute; left: 0; bottom: 0; width: 380px; height: 100px;
  }
  .tagline {
    position: absolute; left: 22px; bottom: 22px;
    color: var(--ink-light); font-size: 9.5px; font-weight: 600;
  }

  /* Inside */
  .panel--inside {
    background: linear-gradient(160deg, var(--cream) 0%, var(--cream-deep) 100%);
  }
  .panel--inside .brand-ghost { top: 110px; color: rgba(154,27,36,.06); }
  .panel--inside-left { border-right: 1px solid rgba(122,18,27,.12); }
  .pocket {
    position: absolute;
    left: 0; bottom: 0;
    width: 380px; height: 200px;
    background: linear-gradient(165deg, var(--crimson-light), var(--crimson-deep));
    box-shadow: 0 -4px 10px rgba(0,0,0,.12);
  }
  .pocket--left { clip-path: polygon(0 0, 100% 18%, 100% 100%, 0 100%); }
  .pocket--right { clip-path: polygon(0 18%, 100% 0, 100% 100%, 0 100%); }
  .pocket__message {
    position: absolute; left: 26px; right: 26px; top: 56px;
    color: var(--ink-light);
    font-size: 8.6px; line-height: 1.55; text-align: left;
  }
  .pocket__contact {
    position: absolute; left: 0; right: 0; top: 66px;
    text-align: center;
  }
  .phone {
    display: inline-flex; align-items: center; gap: 10px;
    color: var(--ink-light); font-size: 22px; font-weight: 700; letter-spacing: .5px;
  }
  .phone::before, .phone::after {
    content: ""; width: 34px; height: 3px;
    border-top: 1px solid var(--ink-light); border-bottom: 1px solid var(--ink-light);
  }
  .thanks {
    margin-top: 10px;
    color: var(--gold-text); font-size: 12px; font-weight: 500; line-height: 1.45;
  }
</style>
</head>
<body>
  <section class="spread spread--outside" aria-label="Folder outside">
    <div class="panel panel--back">
      <div class="brand-ghost" aria-hidden="true">HARBEL<br>TRADEWORKS</div>
      <div class="services">
        <p class="services__title">WE PROVIDE</p>
        <p class="services__list">
          Solar - Generators - Home Security - Home Automation<br>
          Home Inspection - Energy Audits - 1 Day Bathroom remodles<br>
          Basement Waterproofing - Garage Doors - Home Theaters
        </p>
        <p class="services__badge">A graphic that says 24-7 service</p>
      </div>
    </div>

    <div class="panel panel--front">
      <div class="brand-mark">
        <span class="brand-mark__dot"></span>
        <h1 class="brand-mark__name">Harbel<br>Tradeworks</h1>
      </div>
      <svg class="wave-band" viewBox="0 0 380 100" preserveAspectRatio="none" aria-hidden="true">
        <path d="M0 48 C120 70 260 58 380 12 L380 20 C260 66 120 78 0 56 Z" fill="var(--orange)"/>
        <path d="M0 58 C120 80 260 70 380 26 L380 100 L0 100 Z" fill="var(--crimson)"/>
        <path d="M0 62 C120 84 260 74 380 30" fill="none" stroke="#fff" stroke-opacity=".5" stroke-width="1.2"/>
      </svg>
      <p class="tagline">The Best Way To Live In New Jersey Is With Harbel"</p>
    </div>
  </section>

  <section class="spread spread--inside" aria-label="Folder inside">
    <div class="panel panel--inside panel--inside-left">
      <div class="brand-ghost" aria-hidden="true">HARBEL<br>TRADEWORKS</div>
      <div class="pocket pocket--left">
        <p class="pocket__message">Our name says it all, because for over 30 years we have prided ourselves on delivering the best service and exceeding our customers' expectations everyday. Whether you need something fixed, replaced or upgraded, no matter how large or small, the dedicated and experts at Harbel Tradeworks are here to take care of you. Delivering the right solution for you the first time- everytime - and ensuring you are always 100% satisfied. If for any reason you want to speak with us, please do not hesitate to call or email. Thank you again for choosing Harbel Tradeworks.</p>
      </div>
    </div>

    <div class="panel panel--inside">
      <div class="brand-ghost" aria-hidden="true">HARBEL<br>TRADEWORKS</div>
      <div class="pocket pocket--right">
        <div class="pocket__contact">
          <p class="phone">973-555-0148</p>
          <p class="thanks">We want to thank you for choosing<br>Harbel Tradeworks today</p>
        </div>
      </div>
    </div>
  </section>
</body>
</html>
```